Redesign of LumoWordfind.com in Bootstrap 4

Current design of LumoWordfind.com is not responsive. We need to change it to latest version of Bootstrap 4 keeping essential elements in place.

Apart from home page, we need designs for http://www.lumowordfind.com/meaning/cat also.

Coding

Number of Pages Required

2 page

Colors
34a7d8

Requirements
Must have
• Bootstrap 4

```html
<!DOCTYPE html>
<html lang="en">
<head>
<meta charset="utf-8">
<title>Lumo Wordfind – Home</title>
<link href="https://fonts.googleapis.com/css2?family=Open+Sans:wght@400;600;700&display=swap" rel="stylesheet">
<style>
:root{
  --brand:#34a7d8;
  --brand-dark:#1f7fa9;
  --accent:#f5a31a;
  --red:#e9575a;
  --text:#555;
  --light:#f4f9fc;
  --line:#e6e6e6;
  --white:#fff;
}
*{box-sizing:border-box;margin:0;padding:0}
html,body{width:800px;height:1200px;overflow:hidden}
body{font-family:"Open Sans",Arial,sans-serif;color:var(--text);background:var(--white);position:relative}
.abs{position:absolute}

/* header */
.site-header{position:absolute;left:0;top:0;width:800px;height:77px;background:linear-gradient(180deg,#eaf5fb,#f9fcfe)}
.brand{left:68px;top:22px;display:flex;align-items:center;gap:6px;font-weight:700;font-size:16px;color:var(--brand-dark)}
.brand-dot{width:14px;height:14px;border-radius:50%;background:var(--accent)}
.join-badge{left:348px;top:14px;width:48px;height:48px}
.login-label{font-size:7.5px;color:#555}
.login-input{height:18px;border:1px solid #ddd;background:#fff}
.login-btn{left:415px;top:40px;width:61px;height:21px;background:var(--accent);color:#fff;font-size:8px;display:flex;align-items:center;justify-content:center}
.forgot{left:488px;top:46px;font-size:6.5px;color:var(--red)}

/* nav */
.main-nav{position:absolute;left:0;top:77px;width:800px;height:33px;background:var(--brand)}
.nav-item{position:absolute;top:12px;font-size:7.5px;font-weight:600;color:#fff;letter-spacing:.2px}
.nav-item.active{color:var(--accent)}
.nav-sep{position:absolute;top:0;width:1px;height:33px;background:rgba(255,255,255,.18)}
.nav-search{left:578px;top:6px;width:156px;height:20px;background:#fff;border:1px solid #ccc;display:flex}
.nav-search span{flex:1;font-size:7.5px;color:#ddd;padding:5px 8px}
.nav-search i{width:30px;border-left:1px solid #ddd;display:flex;align-items:center;justify-content:center}

/* hero */
.hero{position:absolute;left:0;top:110px;width:800px;height:220px;background:radial-gradient(ellipse at 50% 40%,#8bc35a,#5f9a3c 55%,#6f6a5a 100%);border-bottom:3px solid #444}
.hero-title{position:absolute;left:0;width:800px;top:30px;text-align:center;color:#fff;font-size:18px;font-weight:700}
.hero-search{position:absolute;left:220px;top:68px;width:360px;height:28px;display:flex;border:1px solid rgba(255,255,255,.5)}
.hero-search span{flex:1;background:rgba(255,255,255,.15);color:#fff;font-size:10px;padding:7px 16px}
.hero-search b{width:64px;background:var(--red);color:#fff;font-size:10px;font-weight:600;display:flex;align-items:center;justify-content:center}
.hero-hint{position:absolute;left:220px;top:106px;font-size:6px;color:#fff}

/* cards */
.card{position:absolute;width:309px;height:160px}
.card-head{height:29px;background:var(--brand);color:#fff;font-size:11.5px;font-weight:600;padding:6px 20px;position:relative;letter-spacing:.3px}
.card-head::before,.card-head::after{content:"";position:absolute;bottom:-4px;border-top:4px solid var(--brand-dark)}
.card-head::before{left:0;border-right:4px solid transparent}
.card-head::after{right:0;border-left:4px solid transparent}
.card-media{position:absolute;left:2px;top:50px;width:125px;height:116px;border:2px solid #f1f1f1}
.card-title{position:absolute;left:141px;top:56px;font-size:11px;font-weight:600;color:var(--brand)}
.card-text{position:absolute;left:141px;top:80px;width:170px;font-size:8px;line-height:13.6px;color:#555}
.card-btn{position:absolute;left:142px;top:133px;width:70px;height:21px;background:var(--brand);color:#fff;font-size:8px;font-weight:600;display:flex;align-items:center;justify-content:center}
.ticks{list-style:none;position:absolute;left:141px;top:81px;font-size:7px;line-height:14.2px;color:#555}
.ticks li{padding-left:12px;position:relative}
.ticks li::before{content:"";position:absolute;left:1px;top:4px;width:5px;height:3px;border-left:1.5px solid var(--red);border-bottom:1.5px solid var(--red);transform:rotate(-45deg)}
.divider{position:absolute;left:66px;width:668px;height:1px;background:var(--line)}

/* alphabet */
.browse{left:66px;top:950px;width:90px;height:22px;border:1px solid var(--line);font-size:7.5px;color:var(--brand);display:flex;align-items:center;justify-content:center}
.letters{position:absolute;left:167px;top:953px;display:flex;gap:5.9px}
.letters span{width:16px;height:16px;border:1px solid #f3b5b6;border-radius:50%;font-size:7px;color:var(--red);display:flex;align-items:center;justify-content:center}

/* footer */
.site-footer{position:absolute;left:0;top:987px;width:800px;height:213px;background:var(--brand);color:#fff}
.f-col{position:absolute;top:26px}
.f-col h4{font-size:8px;font-weight:700;margin-bottom:16px}
.f-col a{display:block;font-size:7px;color:#fff;text-decoration:none;line-height:15.6px}
.f-sep{position:absolute;top:20px;width:1px;height:145px;background:rgba(255,255,255,.12)}
.news-input{width:159px;height:24px;background:#fff;color:#999;font-size:7px;padding:7px 11px;margin-top:-4px;position:relative}
.news-input::after{content:"›";position:absolute;right:8px;top:3px;color:var(--red);font-size:12px}
.follow{margin-top:22px;font-size:8px;font-weight:700}
.socials{display:flex;gap:9px;margin-top:15px}
.socials span{width:26px;height:26px;border-radius:50%;border:2px solid #fff}
.f-bottom{position:absolute;left:66px;top:170px;width:668px;border-top:1px solid rgba(255,255,255,.2);text-align:center;font-size:7.5px;padding-top:15px}
</style>
</head>
<body>

<header class="site-header">
  <div class="abs brand"><span class="brand-dot"></span>Lumo Wordfind</div>
  <svg class="abs join-badge" viewBox="0 0 48 48" aria-hidden="true">
    <polygon fill="#e9575a" points="24,0 28,7 35,3 36,11 44,10 41,18 48,22 42,27 46,34 38,35 38,43 31,40 27,48 23,41 17,47 15,39 7,40 9,32 1,29 7,23 1,17 9,14 7,6 15,8 17,1 22,7"/>
    <text x="24" y="23" text-anchor="middle" fill="#fff" font-size="6.5" font-family="Open Sans,sans-serif">Join for</text>
    <text x="24" y="31" text-anchor="middle" fill="#fff" font-size="6.5" font-weight="700" font-family="Open Sans,sans-serif">FREE!</text>
  </svg>
  <span class="abs login-label" style="left:414px;top:20px">Enter User Name:</span>
  <span class="abs login-input" style="left:486px;top:15px;width:85px"></span>
  <span class="abs login-label" style="left:582px;top:20px">Enter Password:</span>
  <span class="abs login-input" style="left:648px;top:15px;width:86px"></span>
  <div class="abs login-btn">LOGIN</div>
  <span class="abs forgot">Forgot Password?</span>
</header>

<nav class="main-nav">
  <span class="nav-item active" style="left:87px">HOME</span>
  <span class="nav-sep" style="left:135px"></span>
  <span class="nav-item" style="left:153px">IDIOMS</span>
  <span class="nav-sep" style="left:203px"></span>
  <span class="nav-item" style="left:222px">COMMON ERRORS</span>
  <span class="nav-sep" style="left:315px"></span>
  <span class="nav-item" style="left:335px">CROSSWORD</span>
  <span class="nav-sep" style="left:406px"></span>
  <span class="nav-item" style="left:426px">BLOG</span>
  <span class="nav-sep" style="left:470px"></span>
  <span class="nav-item" style="left:490px">CONTACT</span>
  <span class="nav-sep" style="left:550px"></span>
  <div class="abs nav-search"><span>Search Here</span><i><svg width="8" height="8" viewBox="0 0 10 10"><circle cx="4" cy="4" r="3" fill="none" stroke="#f5a31a" stroke-width="1.5"/><line x1="6.2" y1="6.2" x2="9" y2="9" stroke="#f5a31a" stroke-width="1.5"/></svg></i></div>
</nav>

<section class="hero" role="img" aria-label="Open book with grass growing on its pages">
  <h1 class="hero-title">Lumo English Wordfind</h1>
  <div class="hero-search"><span>Enter a Word or Phrase</span><b>Search</b></div>
  <p class="hero-hint">(eg. sonnet, metaphor, tattoo)</p>
</section>

<article class="card" style="left:66px;top:356px">
  <div class="card-head">Word of the Day</div>
  <div class="card-media" role="img" aria-label="Hand turning pages of a dictionary" style="background:linear-gradient(135deg,#3f8a86,#c9d6d6 60%,#f1f1f1)"></div>
  <div class="card-title">Ascendancy <svg width="9" height="8" viewBox="0 0 10 9"><polygon points="0,3 3,3 6,0 6,9 3,6 0,6" fill="#e9575a"/><path d="M7.5 2.5q1.5 2 0 4" stroke="#e9575a" fill="none"/></svg></div>
  <p class="card-text">(n) the state that exists when one person or group has power over another</p>
  <div class="card-btn">Show Word</div>
</article>

<article class="card" style="left:425px;top:356px">
  <div class="card-head">Search, Save and Master Words</div>
  <div class="card-media" role="img" aria-label="Set of dark blue reference book volumes" style="background:linear-gradient(90deg,#1e2257,#2b2f78 60%,#1a1c48)"></div>
  <div class="card-title">Master Words!</div>
  <ul class="ticks">
    <li>Search from more than 300,000 words</li>
    <li>Multiple usages to clarify the context</li>
    <li>Audio, phonetics, meanings, synonyms</li>
    <li>It's FREE</li>
  </ul>
  <div class="card-btn" style="top:139px">Read More</div>
</article>

<div class="divider" style="top:538px"></div>

<article class="card" style="left:66px;top:556px">
  <div class="card-head">English Tidbit</div>
  <div class="card-media" role="img" aria-label="Stack of old books with an open fanned book on top" style="background:linear-gradient(160deg,#e9e3dc,#b58a5a 55%,#6b4a2c)"></div>
  <div class="card-title">Search, Save and Master Words</div>
  <p class="card-text">"Gaffe" is a social blunder and "gaff" is a large hook. Be warned not to make the gaffe of mixing it up with gaff.</p>
  <div class="card-btn">Get it Now</div>
</article>

<article class="card" style="left:425px;top:556px">
  <div class="card-head">Daily Crossword</div>
  <div class="card-media" role="img" aria-label="Pencil resting on a crossword grid" style="background:linear-gradient(135deg,#e6e6e6,#9a9a9a 60%,#d8d8d8)"></div>
  <div class="card-title">Crossword Lovers!</div>
  <p class="card-text" style="top:82px">Take this daily crossword challenge from Lumo Wordfind.</p>
  <div class="card-btn">Solve Now</div>
</article>

<div class="divider" style="top:738px"></div>

<article class="card" style="left:66px;top:752px">
  <div class="card-head">Emberfox Addon</div>
  <div class="card-media" role="img" aria-label="Browser addon promotional artwork" style="background:linear-gradient(180deg,#1f5ea8,#2f7fcf 55%,#e07a1f)"></div>
  <div class="card-title">Quickly Emberfox!</div>
  <p class="card-text">Add this tool to your Emberfox and quickly look up for definitions from any website without leaving the page.</p>
  <div class="card-btn">Get it Now</div>
</article>

<article class="card" style="left:425px;top:752px">
  <div class="card-head">Designed for Nimbus Phone</div>
  <div class="card-media" role="img" aria-label="Hand holding a smartphone" style="background:linear-gradient(135deg,#f3d27a,#e7e3de 50%,#5a8fc0)"></div>
  <div class="card-title">Nimbus Phone Lookup!</div>
  <p class="card-text">Lumo Wordfind is specially designed for your Nimbus Phone to quickly lookup meaning, usages and audio of words.</p>
  <div class="card-btn">Get it Now</div>
</article>

<div class="divider" style="top:936px"></div>

<div class="abs browse">Browse Dictionary</div>
<div class="letters">
  <span>A</span><span>B</span><span>C</span><span>D</span><span>E</span><span>F</span><span>G</span><span>H</span><span>I</span><span>J</span><span>K</span><span>L</span><span>M</span><span>N</span><span>O</span><span>P</span><span>Q</span><span>R</span><span>S</span><span>T</span><span>U</span><span>V</span><span>W</span><span>X</span><span>Y</span><span>Z</span>
</div>

<footer class="site-footer">
  <div class="f-col" style="left:66px">
    <h4>LUMOWORDFIND.COM</h4>
    <a>Home</a><a>Idioms</a><a>Common Errors</a><a>Crossword</a><a>Blog</a><a>Contact</a>
  </div>
  <span class="f-sep" style="left:203px"></span>
  <div class="f-col" style="left:248px">
    <h4>LEGAL</h4>
    <a>FAQ</a><a>Contact</a><a>Blog</a><a>Privacy Policy</a><a>Terms of Use</a>
  </div>
  <span class="f-sep" style="left:348px"></span>
  <div class="f-col" style="left:402px">
    <h4>OTHERS</h4>
    <a>Popular Words</a><a>Common Errors in English</a><a>Skill Test Online</a><a>Wordfind</a>
  </div>
  <span class="f-sep" style="left:532px"></span>
  <div class="f-col" style="left:574px">
    <h4>NEWSLETTER SIGN UP</h4>
    <div class="news-input">Enter you Email</div>
    <div class="follow">FOLLOW US</div>
    <div class="socials">
      <span style="background:#3b5a9a"></span><span style="background:#29b6d8"></span><span style="background:#f0a020"></span><span style="background:#e02020"></span>
    </div>
  </div>
  <div class="f-bottom">LUMO WORDFIND. © 2016 | Privacy Policy</div>
</footer>

</body>
</html>
```